Business Card Design for company

We want new business cards. We'd like something different-- yet still highly professional. Our tagline is Providing leadership, delivering success. Stock photos are ok, as long as they are relevant and look upscale.

Target Market(s)

Architecture/Business Management Consulting/Engineering Consulting

Contact Information for Business Card

dark gray background with pops of blue might be good, but you tell me. You're the designers. Rounded corners might be nice, but again, you tell me.

Font styles to use
Serif
Sans Serif

Colors
3276b5
5c5c5c
9d9d9d
fbfbfb

Requirements
Nice to have
• Something different, but still very professional.

```html
<!DOCTYPE html>
<html lang="en">
<head>
<meta charset="utf-8">
<title>Corvane Partners – Business Cards</title>
<link rel="stylesheet" href="https://fonts.googleapis.com/css2?family=Montserrat:wght@400;500;700&family=Roboto:wght@400&display=swap">
<style>
  :root {
    --blue: #3276b5;
    --ink: #5c5c5c;
    --mid: #9d9d9d;
    --paper: #fbfbfb;
    --band: #4a4c50;
    --stage: #e6e7e9;
    --map: #e9eaec;
  }
  * { box-sizing: border-box; margin: 0; padding: 0; }
  html, body { width: 1200px; height: 900px; overflow: hidden; }
  body {
    background: var(--stage);
    font-family: "Montserrat", sans-serif;
    color: var(--ink);
    display: flex;
    flex-direction: column;
    align-items: center;
    justify-content: center;
    gap: 48px;
  }
  .card {
    position: relative;
    width: 630px;
    height: 360px;
    background: var(--paper);
    box-shadow: 0 10px 28px rgba(0,0,0,0.18);
    overflow: hidden;
  }
  .world-map {
    position: absolute;
    background: radial-gradient(ellipse at 50% 45%, #e2e3e6 0%, var(--map) 55%, var(--paper) 85%);
  }
  /* Front */
  .card-front .world-map { left: 60px; top: 20px; width: 510px; height: 300px; }
  .front-brand {
    position: absolute;
    left: 0; right: 0; top: 110px;
    text-align: center;
  }
  .brand-name {
    font-weight: 700;
    color: var(--blue);
    letter-spacing: 0.04em;
    text-transform: uppercase;
  }
  .card-front .brand-name { font-size: 52px; line-height: 1; }
  .brand-line {
    font-weight: 500;
    color: var(--ink);
    letter-spacing: 0.12em;
    text-transform: uppercase;
  }
  .card-front .brand-line { font-size: 26px; margin-top: 12px; }
  .tagline {
    position: absolute;
    left: 0; right: 0; bottom: 44px;
    text-align: center;
    font-size: 12px;
    font-weight: 500;
    letter-spacing: 0.16em;
    text-transform: uppercase;
    color: var(--ink);
  }
  /* Back */
  .card-back .world-map { left: 20px; top: 30px; width: 560px; height: 230px; }
  .back-brand {
    position: absolute;
    left: 40px; top: 118px;
    width: 250px;
    text-align: center;
  }
  .card-back .brand-name { font-size: 34px; line-height: 1; }
  .card-back .brand-line { font-size: 17px; margin-top: 8px; }
  .divider {
    position: absolute;
    left: 312px; top: 72px;
    width: 1.5px; height: 170px;
    background: var(--blue);
  }
  .contact {
    position: absolute;
    left: 334px; top: 62px;
  }
  .person-name {
    font-size: 21px;
    font-weight: 700;
    color: var(--blue);
    letter-spacing: 0.02em;
    text-transform: uppercase;
  }
  .person-role {
    font-size: 13px;
    font-weight: 500;
    color: #333;
    margin-bottom: 10px;
  }
  .contact-list { list-style: none; }
  .contact-list li {
    display: flex;
    align-items: center;
    gap: 8px;
    font-family: "Roboto", sans-serif;
    font-size: 13.5px;
    line-height: 22px;
    color: #3c3c3c;
  }
  .contact-list svg { width: 11px; height: 11px; flex: none; }
  .address-band {
    position: absolute;
    left: 0; right: 0; bottom: 0;
    height: 58px;
    background: var(--band);
    border-top: 3px solid var(--blue);
    box-shadow: 0 -5px 0 var(--paper), 0 -6.5px 0 var(--blue);
    display: flex;
    align-items: center;
    justify-content: center;
    font-family: "Roboto", sans-serif;
    font-size: 14px;
    color: #ffffff;
    letter-spacing: 0.01em;
  }
</style>
</head>
<body>

  <section class="card card-front">
    <div class="world-map" role="img" aria-label="Faint grey world map in the background"></div>
    <div class="front-brand">
      <div class="brand-name">Corvane</div>
      <div class="brand-line">Partners</div>
    </div>
    <p class="tagline">Providing leadership | Delivering success</p>
  </section>

  <section class="card card-back">
    <div class="world-map" role="img" aria-label="Faint dotted world map in the background"></div>
    <div class="back-brand">
      <div class="brand-name">Corvane</div>
      <div class="brand-line">Partners</div>
    </div>
    <div class="divider"></div>
    <div class="contact">
      <h1 class="person-name">Daniel Ashford</h1>
      <p class="person-role">Design Consultant</p>
      <ul class="contact-list">
        <li>
          <svg viewBox="0 0 12 12"><rect x="3" y="0.5" width="6" height="11" rx="1" fill="none" stroke="#3276b5" stroke-width="1.3"/><circle cx="6" cy="9.5" r="0.7" fill="#3276b5"/></svg>
          555-318-0427
        </li>
        <li>
          <svg viewBox="0 0 12 12"><path d="M2.5 1 L4.5 1 L5.3 3.4 L4 4.4 Q5.2 7 7.6 8 L8.6 6.7 L11 7.5 L11 9.5 Q10.5 11 9 11 Q1 10 1 2.5 Q1 1 2.5 1Z" fill="#3276b5"/></svg>
          01632 960418 (Westbury)
        </li>
        <li>
          <svg viewBox="0 0 12 12"><path d="M2.5 1 L4.5 1 L5.3 3.4 L4 4.4 Q5.2 7 7.6 8 L8.6 6.7 L11 7.5 L11 9.5 Q10.5 11 9 11 Q1 10 1 2.5 Q1 1 2.5 1Z" fill="#3276b5"/></svg>
          01632 960752 (Ashcombe)
        </li>
        <li>
          <svg viewBox="0 0 12 12"><rect x="0.7" y="2.2" width="10.6" height="7.6" rx="1" fill="none" stroke="#3276b5" stroke-width="1.3"/><path d="M1 2.8 L6 6.6 L11 2.8" fill="none" stroke="#3276b5" stroke-width="1.3"/></svg>
          info@corvanepartners.com
        </li>
        <li>
          <svg viewBox="0 0 12 12"><circle cx="6" cy="6" r="5" fill="none" stroke="#3276b5" stroke-width="1.2"/><ellipse cx="6" cy="6" rx="2.2" ry="5" fill="none" stroke="#3276b5" stroke-width="1"/><path d="M1 6 H11" stroke="#3276b5" stroke-width="1"/></svg>
          www.corvanepartners.com
        </li>
      </ul>
    </div>
    <footer class="address-band">Unit 8, The Fenmore Centre, Millbrook Yard, Westbury, Wilts BA9 4QR</footer>
  </section>

</body>
</html>
```